Stationery Design Project

Hi All,

We need you to design stationary for a new Business and Accounting Advisory Firm. We have already got the logo designed and it is attached. If you could also if possible, match the fonts in your design to that on the logo’s provided.

What we need:
- Business Card
- A4 Letter head
- A4 Folders
- PPT template (Title page and regular page)

And what ever else you want to throw in.

We are in the process of getting the web site designed, however below is a list of websites which we like which will give you an understanding of the style that we are going for.

- plivant.example
- moldrabay.example
- tarvenhook.example
- quillorbank.example

I look forward to your seeing your design.
Updates

Hi All,

I have just realised that I forgot that i need to include a Sworn Ledgerkeepers image on the letter head, please find attaced as File 1. Could you please have this image in the bottom left header.

Regards,

Marcus

Industry/Entity Type

Business

Requirements
Must have
• Outputs:
- Documents ready to print
- Generic editable information
- Pdf copies of the documents
- Word version of letterhead

```html
<!DOCTYPE html>
<html lang="en">
<head>
<meta charset="utf-8">
<title>Orrinvale Partners – Stationery Set</title>
<link rel="stylesheet" href="https://fonts.googleapis.com/css2?family=Cormorant+Garamond:ital,wght@0,500;1,500&family=Mulish:wght@400&display=swap">
<style>
  :root {
    --bg: #e9dcc4;
    --paper: #ffffff;
    --orange: #f36c12;
    --amber: #ffb21c;
    --blue: #2d5fd8;
    --cyan: #4fe0e0;
    --brand-text: #2c4fc9;
    --badge: #b01e23;
    --label: #1b1b1b;
  }
  * { box-sizing: border-box; margin: 0; padding: 0; }
  html, body { width: 1200px; height: 1089px; overflow: hidden; }
  body { background: var(--bg); position: relative; font-family: "Mulish", sans-serif; }

  .piece { position: absolute; background: var(--paper); box-shadow: 0 3px 10px rgba(0,0,0,.25); overflow: hidden; }
  .piece > svg.art { position: absolute; inset: 0; width: 100%; height: 100%; }

  .wordmark { position: absolute; display: flex; align-items: center; gap: 10px; }
  .wordmark .dot { border-radius: 50%; background: var(--orange); flex: none; }
  .wordmark .name { font-family: "Cormorant Garamond", serif; font-weight: 500; color: var(--brand-text); line-height: 1; white-space: nowrap; }
  .tagline { font-family: "Mulish", sans-serif; color: var(--brand-text); letter-spacing: .35em; white-space: nowrap; display: block; margin-top: 3px; }

  .badge { position: absolute; border-radius: 50%; background: var(--badge); }

  .label { position: absolute; font-family: "Cormorant Garamond", serif; font-style: italic; font-weight: 500; font-size: 28px; color: var(--label); white-space: nowrap; }

  /* Letterhead */
  .letterhead { left: 160px; top: 15px; width: 400px; height: 566px; }
  .letterhead .wordmark { left: 14px; top: 18px; }
  .letterhead .dot { width: 36px; height: 36px; }
  .letterhead .name { font-size: 27px; }
  .letterhead .tagline { font-size: 9px; }
  .letterhead .badge { right: 16px; bottom: 12px; width: 22px; height: 22px; }

  /* Business cards */
  .card { width: 165px; height: 95px; }
  .card-front { left: 568px; top: 120px; }
  .card-front .wordmark { left: 14px; top: 30px; }
  .card-front .dot { width: 30px; height: 30px; background: var(--amber); }
  .card-front .name { font-size: 20px; color: var(--paper); }
  .card-back { left: 568px; top: 232px; }
  .card-back .wordmark { left: 10px; top: 12px; gap: 6px; }
  .card-back .dot { width: 16px; height: 16px; }
  .card-back .name { font-size: 14px; }
  .card-back .tagline { font-size: 5px; }
  .card-back .badge { left: 8px; bottom: 8px; width: 16px; height: 16px; }

  /* Folder */
  .folder { left: 745px; top: 75px; width: 440px; height: 590px; }
  .folder .wordmark { left: 60px; top: 230px; }
  .folder .dot { width: 56px; height: 56px; }
  .folder .name { font-size: 33px; }
  .folder .tagline { font-size: 11px; }

  /* Envelopes */
  .envelope { width: 520px; height: 290px; }
  .envelope-front { left: 60px; top: 700px; }
  .envelope-front .wordmark { left: 40px; top: 92px; }
  .envelope-front .dot { width: 46px; height: 46px; }
  .envelope-front .name { font-size: 30px; }
  .envelope-front .tagline { font-size: 10px; }
  .envelope-rear { left: 620px; top: 715px; }
  .envelope-rear .wordmark { right: 22px; bottom: 26px; gap: 7px; }
  .envelope-rear .dot { width: 26px; height: 26px; }
  .envelope-rear .name { font-size: 18px; }
  .envelope-rear .tagline { font-size: 6px; }
</style>
</head>
<body>

<svg width="0" height="0" style="position:absolute" aria-hidden="true">
  <defs>
    <linearGradient id="grad-orange" x1="0" y1="0" x2="1" y2="0">
      <stop offset="0" stop-color="#f36c12"/><stop offset="1" stop-color="#ffb21c"/>
    </linearGradient>
    <linearGradient id="grad-blue" x1="0" y1="0" x2="1" y2="0">
      <stop offset="0" stop-color="#2d5fd8"/><stop offset="1" stop-color="#4fe0e0"/>
    </linearGradient>
    <linearGradient id="grad-blue-v" x1="0" y1="0" x2="1" y2="0">
      <stop offset="0" stop-color="#2d5fd8"/><stop offset=".55" stop-color="#3a8fe0"/><stop offset="1" stop-color="#58e6e0"/>
    </linearGradient>
  </defs>
</svg>

<!-- Letterhead -->
<section class="piece letterhead" aria-label="Letterhead">
  <svg class="art" viewBox="0 0 400 566" preserveAspectRatio="none">
    <path d="M0 0H400V70Q200 68 0 85Z" fill="url(#grad-orange)"/>
    <path d="M0 85Q200 62 400 70V85Z" fill="url(#grad-blue)"/>
    <path d="M300 0H400V70Q360 40 300 0Z" fill="url(#grad-blue)" opacity=".9"/>
    <path d="M330 0H345Q370 40 372 68H360Q355 35 330 0Z" fill="url(#grad-orange)"/>
    <path d="M20 512Q220 500 400 430V460Q240 512 20 512Z" fill="url(#grad-orange)"/>
    <path d="M20 518Q240 510 400 455V518Z" fill="url(#grad-blue)"/>
    <rect x="0" y="518" width="400" height="48" fill="#fff"/>
  </svg>
  <div class="wordmark">
    <span class="dot"></span>
    <div><span class="name">Orrinvale Partners</span><span class="tagline">Business Advisors</span></div>
  </div>
  <span class="badge"></span>
</section>

<!-- Business cards -->
<section class="piece card card-front" aria-label="Business card front">
  <svg class="art" viewBox="0 0 165 95" preserveAspectRatio="none">
    <rect width="165" height="95" fill="url(#grad-blue)"/>
  </svg>
  <div class="wordmark"><span class="dot"></span><span class="name">Orrinvale</span></div>
</section>

<section class="piece card card-back" aria-label="Business card back">
  <svg class="art" viewBox="0 0 165 95" preserveAspectRatio="none">
    <rect width="165" height="95" fill="url(#grad-blue)"/>
    <path d="M0 95Q90 80 150 0H165V5Q120 75 40 95Z" fill="url(#grad-orange)"/>
    <path d="M60 95Q130 70 165 20V95Z" fill="#ffb21c"/>
    <path d="M0 70Q30 68 50 95H0Z" fill="#fff"/>
  </svg>
  <div class="wordmark">
    <span class="dot"></span>
    <div><span class="name">Orrinvale Partners</span><span class="tagline">Business Advisors</span></div>
  </div>
  <span class="badge"></span>
</section>

<!-- Folder -->
<section class="piece folder" aria-label="A4 folder">
  <svg class="art" viewBox="0 0 440 590" preserveAspectRatio="none">
    <rect width="440" height="590" fill="url(#grad-blue-v)"/>
    <path d="M360 0H385Q430 280 345 590H318Q405 290 360 0Z" fill="url(#grad-orange)"/>
    <path d="M385 0H440V590H345Q430 280 385 0Z" fill="url(#grad-blue)"/>
  </svg>
  <div class="wordmark">
    <span class="dot"></span>
    <div><span class="name">Orrinvale Partners</span><span class="tagline">Business Advisors</span></div>
  </div>
</section>

<!-- Envelopes -->
<section class="piece envelope envelope-front" aria-label="Envelope front">
  <svg class="art" viewBox="0 0 520 290" preserveAspectRatio="none">
    <path d="M0 0H520V55Q260 55 0 62Z" fill="url(#grad-orange)"/>
    <path d="M0 200Q60 215 95 290H0Z" fill="url(#grad-orange)"/>
    <rect x="410" y="80" width="32" height="210" fill="url(#grad-blue)"/>
    <rect x="448" y="80" width="32" height="210" fill="url(#grad-orange)"/>
  </svg>
  <div class="wordmark">
    <span class="dot"></span>
    <div><span class="name">Orrinvale Partners</span><span class="tagline">Business Advisors</span></div>
  </div>
</section>

<section class="piece envelope envelope-rear" aria-label="Envelope rear">
  <svg class="art" viewBox="0 0 520 290" preserveAspectRatio="none">
    <path d="M0 0H520V40Q260 60 0 75Z" fill="url(#grad-orange)"/>
    <path d="M0 215Q60 225 100 290H0Z" fill="url(#grad-orange)"/>
  </svg>
  <div class="wordmark">
    <span class="dot"></span>
    <div><span class="name">Orrinvale Partners</span><span class="tagline">Business Advisors</span></div>
  </div>
</section>

<span class="label" style="left:590px;top:72px">Business Card</span>
<span class="label" style="left:10px;top:478px">Letter head</span>
<span class="label" style="left:605px;top:640px">A4 Folders</span>
<span class="label" style="left:60px;top:1005px">envelope front</span>
<span class="label" style="left:660px;top:1030px">envelope rear</span>

</body>
</html>
```